Business Card Design Project

Business Card
We are rebranding with a new logo
Industry/Entity Type
Business
Contact Information for Business Card
Dennis Morvale +61 487215963 dennis@quorv.com.au P.O. Box 872 Fernlow QLD 4309
Requirements
Must have
- Logo

```html
<!DOCTYPE html>
<html lang="en">
<head>
<meta charset="utf-8">
<title>Quorv International – Business Card</title>
<link href="https://fonts.googleapis.com/css2?family=Montserrat:wght@600;700&family=Quicksand:wght@500;600&display=swap" rel="stylesheet">
<style>
  :root {
    --ink: #1b1b1b;
    --blue: #1a8fc9;
    --orange: #f28a1e;
    --card: #ffffff;
    --backdrop: #d9d9d9;
  }
  * { box-sizing: border-box; margin: 0; padding: 0; }
  html, body { width: 1200px; height: 800px; overflow: hidden; }
  body {
    background: var(--backdrop);
    display: flex;
    align-items: center;
    justify-content: center;
    gap: 60px;
    font-family: "Quicksand", sans-serif;
    color: var(--ink);
  }
  .card {
    position: relative;
    width: 500px;
    height: 286px;
    background: var(--card);
    box-shadow: 0 6px 18px rgba(0,0,0,.18);
  }
  .card-front { display: flex; align-items: center; justify-content: center; }
  .brand {
    display: flex;
    align-items: center;
    gap: 12px;
    font-family: "Montserrat", sans-serif;
    font-weight: 700;
    color: var(--blue);
  }
  .brand-mark { width: 22px; height: 22px; background: var(--orange); }
  .brand-front .brand-name { font-size: 30px; letter-spacing: 1px; }
  .brand-back { position: absolute; top: 62px; right: 24px; gap: 6px; }
  .brand-back .brand-name { font-size: 13px; }
  .brand-back .brand-mark { width: 10px; height: 10px; }

  .side-band {
    position: absolute;
    left: 52px; top: 0;
    width: 46px; height: 100%;
    background: var(--orange);
  }
  .monogram {
    position: absolute;
    left: 42px; top: 64px;
    width: 66px; height: 42px;
    background: var(--blue);
    border: 4px solid var(--card);
    color: #fff;
    font-family: "Montserrat", sans-serif;
    font-weight: 700;
    font-size: 19px;
    display: flex; align-items: center; justify-content: center;
  }
  .person-name {
    position: absolute;
    left: 126px; top: 64px;
    font-family: "Montserrat", sans-serif;
    font-weight: 700;
    font-size: 19px;
    color: var(--orange);
    text-transform: uppercase;
  }
  .contact-list { position: absolute; left: 0; top: 120px; list-style: none; width: 100%; }
  .contact-item {
    display: flex; align-items: center;
    height: 34px;
    font-size: 13px; font-weight: 600;
  }
  .contact-icon { width: 46px; margin-left: 52px; display: flex; justify-content: center; }
  .contact-icon svg { width: 14px; height: 14px; fill: none; stroke: #fff; stroke-width: 1.6; }
  .contact-text { margin-left: 28px; }
</style>
</head>
<body>
  <section class="card card-front">
    <div class="brand brand-front">
      <span class="brand-mark"></span>
      <span class="brand-name">Quorv International</span>
    </div>
  </section>

  <section class="card card-back">
    <div class="side-band"></div>
    <div class="monogram">DM</div>
    <h1 class="person-name">Dennis Morvale</h1>
    <div class="brand brand-back">
      <span class="brand-mark"></span>
      <span class="brand-name">Quorv International</span>
    </div>
    <ul class="contact-list">
      <li class="contact-item">
        <span class="contact-icon"><svg viewBox="0 0 14 14"><rect x="3" y="1" width="8" height="12" rx="1.5"/><line x1="6" y1="11" x2="8" y2="11"/></svg></span>
        <span class="contact-text">+61 487215963</span>
      </li>
      <li class="contact-item">
        <span class="contact-icon"><svg viewBox="0 0 14 14"><rect x="1" y="3" width="12" height="8"/><polyline points="1,3 7,8 13,3"/></svg></span>
        <span class="contact-text">dennis@quorv.com.au</span>
      </li>
      <li class="contact-item">
        <span class="contact-icon"><svg viewBox="0 0 14 14"><path d="M7 13 C3 8 3 6.5 3 5.5 a4 4 0 0 1 8 0 c0 1 0 2.5 -4 7.5z"/><circle cx="7" cy="5.5" r="1.4"/></svg></span>
        <span class="contact-text">P.O. Box 872 Fernlow QLD 4309</span>
      </li>
    </ul>
  </section>
</body>
</html>
```